Healthcare/Medical Consultant Company

QRN is a Healthcare Conultant Company. We help doctors manage the business side of their medical practice.
We already have a very basic world press design. We want an upgraded design that conveys partnership, healthcare expertise and healthcare innovation to our client. It needs to have a sleek, clean, modern and inclusive look. Pictures need need to convey diversity (including pictures of people of all races and shows both men and women working together in a healthcare environment to make it better). The Pictures on the home page should particularly illustrate diversity and Healthcare expertise. The company logo is blue and white but the site doesn’t have to follow the exact same theme but the logo needs to blend well with the chosen theme. The logo should ideally be in the header of the website. We would also like the following included in our website:

1. Pages should include: a home page, About Us page, Services page, Get a quote page, Contact Us page, Staff page(where we can add pictures and bio for staff).

2. The Drop down menu for services should have hyperlinks ( for each service)Leading to a page that provides detailed info about that specific service. Our services include: Revenue Cycle Management, Regulatory Compliance, Human Resources Management, & practice Management.

3. Links to social media should in the header or footer of each page.

4. Contact info should be in the footer of each page.

5. Clients should be an email to us from the contact page.

Target Market(s)

Physician Medical Practices

Industry/Entity Type

Medical

Coding

Coded - Design and coding required

Font styles to use
Sans Serif

Colors

Designer to choose colors to be used in the design.

Requirements
Must have
• See project description
Nice to have
• See project description

```html
<!DOCTYPE html>
<html lang="en">
<head>
<meta charset="utf-8">
<title>QRN – Quill Ridge Network LLC</title>
<link href="https://fonts.googleapis.com/css2?family=Montserrat:wght@400;600;700&family=Lato:wght@400;700&display=swap" rel="stylesheet">
<style>
:root{
  --blue:#2f9fd8;
  --blue-light:#45ace0;
  --navy:#0b4c9c;
  --navy-dark:#083b7c;
  --ink:#333;
  --muted:#666;
  --grey-box:#efefef;
  --dark:#2b2b2b;
  --white:#fff;
}
*{box-sizing:border-box;margin:0;padding:0}
html,body{width:1200px;height:3495px;overflow:hidden}
body{position:relative;font-family:"Lato",sans-serif;color:var(--ink);background:var(--white)}
a{text-decoration:none}
.abs{position:absolute}
h1,h2,h3{font-family:"Montserrat",sans-serif}

/* header */
.brand{left:0;width:1200px;top:14px;text-align:center}
.brand-mark{font-family:"Montserrat",sans-serif;font-weight:700;font-size:44px;color:var(--navy);line-height:48px;letter-spacing:2px}
.brand-name{font-family:"Montserrat",sans-serif;font-weight:700;font-size:14px;color:var(--navy);line-height:18px}
.main-nav{left:77px;top:116px;width:1044px;height:50px;background:linear-gradient(90deg,var(--blue),var(--blue-light));display:flex;z-index:2}
.main-nav a{color:var(--white);font-family:"Montserrat",sans-serif;font-size:15px;line-height:50px;padding:0 25px}
.main-nav a.active{background:var(--navy)}
.main-nav .nav-quote{margin-left:auto;background:var(--navy);font-weight:600;font-size:18px;padding:0 28px}

/* hero */
.hero{left:0;top:147px;width:1200px;height:553px;background:linear-gradient(90deg,#5b6e80 0%,#8ea3b5 35%,#c9d6e0 60%,#eef2f5 100%)}
.hero-title{left:780px;top:312px;font-size:40px;line-height:52px;font-weight:700;color:var(--navy);letter-spacing:1px}
.hero-sub{left:780px;top:480px;width:370px;font-family:"Lato",sans-serif;font-size:19px;line-height:32px;color:#222}

/* section headings */
.section-title{left:0;width:1200px;text-align:center;font-size:40px;font-weight:700;color:var(--navy)}
.section-title span{color:var(--blue)}

/* about */
.about-text{left:245px;width:710px;text-align:center;font-size:15px;line-height:25px;color:var(--muted)}
.btn{display:block;background:var(--navy);color:var(--white);text-align:center;font-family:"Montserrat",sans-serif;font-weight:700;font-size:20px}

/* services */
.services-photo{left:500px;top:1167px;width:700px;height:438px;background:linear-gradient(90deg,#a7b3bd,#7f8c97 60%,#6c7883)}
.services-panel{left:0;top:1137px;width:500px;height:501px;background:rgba(47,159,216,.92)}
.services-title{left:81px;top:1268px;font-size:41px;line-height:52px;font-weight:700;color:var(--white)}
.services-sub{left:81px;top:1390px;width:260px;font-size:15px;line-height:21px;color:var(--white)}
.pager{top:1463px;height:42px;border:1px solid var(--white);color:var(--white);font-family:"Montserrat",sans-serif;font-size:15px;display:flex;align-items:center;justify-content:center;gap:12px}
.service-card{top:1263px;width:238px;height:249px;background:var(--white)}
.service-card .thumb{height:175px;background:linear-gradient(135deg,#dfe5ea,#9aa7b2)}
.service-card .label{display:flex;align-items:center;gap:14px;padding:10px 10px;height:74px}
.service-card .label svg{flex:none}
.service-card .label p{color:var(--blue);font-size:18px;line-height:25px}

/* team */
.team-frame{top:1771px;width:263px;height:407px;border:1px solid #d8d8d8;background:var(--white)}
.team-photo{top:1801px;width:324px;height:210px}
.team-name{top:2043px;width:263px;text-align:center;font-family:"Montserrat",sans-serif;font-weight:400;font-size:19px;color:#444}
.team-bio{top:2072px;width:263px;text-align:center;font-size:15px;line-height:24px;color:var(--muted);padding:0 30px}
.team-social{top:2136px;width:263px;display:flex;justify-content:center;gap:14px}
.team-social a{font-family:"Lato",sans-serif;font-weight:700;font-size:12px;line-height:18px;color:#555}
.arrow-btn{top:2214px;width:40px;height:40px;background:var(--navy);display:flex;align-items:center;justify-content:center}

/* quote band */
.quote-band{left:0;top:2325px;width:1200px;height:210px;background:linear-gradient(90deg,#1f2327,#3a4148 60%,#4b535b)}
.quote-title{left:80px;top:2370px;font-size:36px;font-weight:700;color:var(--white)}
.quote-text{left:80px;top:2428px;width:580px;font-size:15px;line-height:23px;color:var(--white)}
.quote-btn{left:872px;top:2414px;width:251px;height:51px;background:var(--blue);color:var(--white);font-family:"Montserrat",sans-serif;font-weight:700;font-size:20px;line-height:51px;text-align:center}

/* blog */
.blog-img{background:linear-gradient(135deg,#c7d3dc,#7f97aa)}
.blog-box{background:var(--grey-box);padding:22px 20px}
.blog-date{display:flex;align-items:center;gap:8px;font-size:15px;color:#555}
.blog-head{margin-top:10px;font-family:"Lato",sans-serif;font-weight:400;font-size:19px;line-height:27px;color:#444}
.blog-body{margin-top:10px;font-size:14px;line-height:22px;color:var(--muted)}

/* footer */
.footer-base{left:0;top:3295px;width:1200px;height:200px;background:var(--dark)}
.contact-bar{left:77px;top:3234px;width:1046px;height:98px;background:var(--blue);display:flex}
.contact-item{flex:1;display:flex;align-items:center}
.contact-item .ico{width:58px;height:98px;background:#2589bd;display:flex;align-items:center;justify-content:center}
.contact-item p{margin-left:22px;color:var(--white);font-size:15px;line-height:24px}
.footer-social{left:0;width:1200px;top:3365px;display:flex;justify-content:center;gap:26px}
.footer-social a{display:flex;align-items:center;gap:8px;color:var(--white);font-family:"Lato",sans-serif;font-weight:700;font-size:14px;line-height:28px}
.footer-social a::before{content:"";display:block;width:26px;height:26px;border:2px solid var(--white);border-radius:50%}
.copyright{left:0;width:1200px;top:3448px;text-align:center;font-size:14px;color:#ddd}
</style>
</head>
<body>

<header>
  <div class="abs brand">
    <div class="brand-mark">QRN</div>
    <div class="brand-name">Quill Ridge Network LLC</div>
  </div>
  <nav class="abs main-nav">
    <a class="active" href="#">HOME</a>
    <a href="#">ABOUT US</a>
    <a href="#">SERVICES</a>
    <a href="#">OUR STAFF</a>
    <a href="#">CONTACT US</a>
    <a class="nav-quote" href="#">GET A FREE QUOTE</a>
  </nav>
</header>

<section>
  <div class="abs hero" role="img" aria-label="Business team of men and women meeting around a table in a bright office"></div>
  <h1 class="abs hero-title">QUILL RIDGE<br>NETWORK LLC</h1>
  <p class="abs hero-sub">Lorem Ipsum is simply dummy text of the printing and typesetting industry.</p>
</section>

<section>
  <h2 class="abs section-title" style="top:745px"><span>ABOUT</span> US</h2>
  <p class="abs about-text" style="top:812px">Lorem Ipsum is simply dummy text of the printing and typesetting industry. Lorem Ipsum has been the industry's standard dummy text ever since the 1500s, when an unknown printer took a galley of type and scrambled it to make a type specimen book. It has survived not only five centuries, but also the leap into electronic typesetting, remaining essentially unchanged.</p>
  <p class="abs about-text" style="top:926px">It was popularised in the 1960s with the release of Setline sheets containing Lorem Ipsum passages, and more recently with desktop publishing software like Folio Typeset including versions of Lorem Ipsum.</p>
  <a class="abs btn" href="#" style="left:382px;top:1000px;width:210px;height:51px;line-height:51px">KNOW MORE</a>
  <a class="abs btn" href="#" style="left:610px;top:1000px;width:208px;height:51px;line-height:51px">CONTACT US</a>
</section>

<section>
  <div class="abs services-photo" role="img" aria-label="Colleagues working together at laptops in an office"></div>
  <div class="abs services-panel"></div>
  <h2 class="abs services-title">OUR<br>SERVICES</h2>
  <p class="abs services-sub">Lorem Ipsum is simply dummy text of the printing and typesetting.</p>
  <div class="abs pager" style="left:77px;width:105px">
    <svg width="22" height="14" viewBox="0 0 22 14"><path d="M21 7H2M8 1L2 7l6 6" fill="none" stroke="#fff" stroke-width="2"/></svg>PRE</div>
  <div class="abs pager" style="left:203px;width:102px">NEXT
    <svg width="22" height="14" viewBox="0 0 22 14"><path d="M1 7h19M14 1l6 6-6 6" fill="none" stroke="#fff" stroke-width="2"/></svg></div>

  <article class="abs service-card" style="left:354px">
    <div class="thumb" role="img" aria-label="Hands with calculator and financial papers"></div>
    <div class="label">
      <svg width="40" height="40" viewBox="0 0 40 40"><circle cx="20" cy="20" r="16" fill="none" stroke="#0b4c9c" stroke-width="2.5"/><text x="20" y="27" text-anchor="middle" font-family="Montserrat,sans-serif" font-weight="700" font-size="20" fill="#0b4c9c">$</text></svg>
      <p>Revenue Cycle Management</p>
    </div>
  </article>
  <article class="abs service-card" style="left:617px">
    <div class="thumb" role="img" aria-label="Medical staff working at a computer"></div>
    <div class="label">
      <svg width="40" height="40" viewBox="0 0 40 40"><rect x="8" y="4" width="24" height="32" rx="2" fill="none" stroke="#0b4c9c" stroke-width="2.5"/><text x="20" y="26" text-anchor="middle" font-family="Montserrat,sans-serif" font-weight="700" font-size="15" fill="#0b4c9c">$</text></svg>
      <p>Medical Billing &amp; Coding</p>
    </div>
  </article>
  <article class="abs service-card" style="left:883px">
    <div class="thumb" role="img" aria-label="Person reviewing documents at a desk"></div>
    <div class="label">
      <svg width="40" height="40" viewBox="0 0 40 40"><rect x="9" y="6" width="22" height="28" rx="2" fill="none" stroke="#0b4c9c" stroke-width="2.5"/><path d="M14 16h12M14 22h8" stroke="#0b4c9c" stroke-width="2"/><circle cx="29" cy="31" r="6" fill="#0b4c9c"/><path d="M26 31l2 2 4-4" fill="none" stroke="#fff" stroke-width="1.8"/></svg>
      <p>Regulatory Compliance</p>
    </div>
  </article>
</section>

<section>
  <h2 class="abs section-title" style="top:1703px"><span>OUR</span> TEAM</h2>

  <div class="abs team-frame" style="left:110px"></div>
  <div class="abs team-photo" role="img" aria-label="Portrait of a team member" style="left:77px;background:linear-gradient(135deg,#b9c4cc,#6f7f8c)"></div>
  <h3 class="abs team-name" style="left:110px">NAME SURNAME</h3>
  <p class="abs team-bio" style="left:110px">Lorem Ipsum is simply dummy text of the printing</p>
  <div class="abs team-social" style="left:110px"><a href="#">Linkora</a><a href="#">Chirpa</a><a href="#">Gplex</a></div>

  <div class="abs team-frame" style="left:471px"></div>
  <div class="abs team-photo" role="img" aria-label="Portrait of a team member" style="left:440px;background:linear-gradient(135deg,#dfe6ec,#8a9aa7)"></div>
  <h3 class="abs team-name" style="left:471px">NAME SURNAME</h3>
  <p class="abs team-bio" style="left:471px">Lorem Ipsum is simply dummy text of the printing</p>
  <div class="abs team-social" style="left:471px"><a href="#">Linkora</a><a href="#">Chirpa</a><a href="#">Gplex</a></div>

  <div class="abs team-frame" style="left:832px"></div>
  <div class="abs team-photo" role="img" aria-label="Portrait of a team member" style="left:801px;background:linear-gradient(135deg,#7a7f84,#4d5358)"></div>
  <h3 class="abs team-name" style="left:832px">NAME SURNAME</h3>
  <p class="abs team-bio" style="left:832px">Lorem Ipsum is simply dummy text of the printing</p>
  <div class="abs team-social" style="left:832px"><a href="#">Linkora</a><a href="#">Chirpa</a><a href="#">Gplex</a></div>

  <div class="abs arrow-btn" style="left:77px"><svg width="18" height="14" viewBox="0 0 18 14"><path d="M17 7H2M7 1L1 7l6 6" fill="none" stroke="#fff" stroke-width="2"/></svg></div>
  <div class="abs arrow-btn" style="left:1083px"><svg width="18" height="14" viewBox="0 0 18 14"><path d="M1 7h15M11 1l6 6-6 6" fill="none" stroke="#fff" stroke-width="2"/></svg></div>
</section>

<section>
  <div class="abs quote-band" role="img" aria-label="Dimmed photo of a business meeting"></div>
  <h2 class="abs quote-title">GET A FREE QUOTE</h2>
  <p class="abs quote-text">Lorem Ipsum is simply dummy text of the printing and typesetting industry. Lorem Ipsum has been the industry's standard dummy text ever since the 1500s.</p>
  <a class="abs quote-btn" href="#">GET A FREE QUOTE</a>
</section>

<section>
  <h2 class="abs section-title" style="top:2580px"><span>LATEST</span> BLOG</h2>

  <div class="abs blog-img" role="img" aria-label="Colleagues talking in a bright office" style="left:77px;top:2650px;width:333px;height:230px"></div>
  <div class="abs blog-img" role="img" aria-label="Team gathered around a laptop" style="left:436px;top:2650px;width:342px;height:230px;background:linear-gradient(135deg,#d9e4ec,#8eaac0)"></div>
  <article class="abs blog-box" style="left:778px;top:2650px;width:345px;height:230px">
    <div class="blog-date"><svg width="16" height="16" viewBox="0 0 16 16"><rect x="1" y="3" width="14" height="12" fill="none" stroke="#777" stroke-width="1.5"/><path d="M1 7h14M5 1v4M11 1v4" stroke="#777" stroke-width="1.5"/></svg>29 May 2017</div>
    <h3 class="blog-head">Lorem Ipsum is simply dummy text of the printing and typesetting.</h3>
    <p class="blog-body">Lorem Ipsum is simply dummy text of the printing and typesetting industry. Lorem Ipsum has been the industry's standard.</p>
  </article>

  <article class="abs blog-box" style="left:77px;top:2903px;width:333px;height:229px">
    <div class="blog-date"><svg width="16" height="16" viewBox="0 0 16 16"><rect x="1" y="3" width="14" height="12" fill="none" stroke="#777" stroke-width="1.5"/><path d="M1 7h14M5 1v4M11 1v4" stroke="#777" stroke-width="1.5"/></svg>29 May 2017</div>
    <h3 class="blog-head">Lorem Ipsum is simply dummy text of the printing and typesetting.</h3>
    <p class="blog-body">Lorem Ipsum is simply dummy text of the printing and typesetting industry. Lorem Ipsum has been the industry's standard.</p>
  </article>
  <article class="abs blog-box" style="left:436px;top:2903px;width:342px;height:229px">
    <div class="blog-date"><svg width="16" height="16" viewBox="0 0 16 16"><rect x="1" y="3" width="14" height="12" fill="none" stroke="#777" stroke-width="1.5"/><path d="M1 7h14M5 1v4M11 1v4" stroke="#777" stroke-width="1.5"/></svg>29 May 2017</div>
    <h3 class="blog-head">Lorem Ipsum is simply dummy text of the printing and typesetting.</h3>
    <p class="blog-body">Lorem Ipsum is simply dummy text of the printing and typesetting industry. Lorem Ipsum has been the industry's standard.</p>
  </article>
  <div class="abs blog-img" role="img" aria-label="Two colleagues working in a modern lounge" style="left:778px;top:2903px;width:345px;height:229px;background:linear-gradient(135deg,#e4ebf0,#7fa6bd)"></div>
</section>

<footer>
  <div class="abs footer-base"></div>
  <div class="abs contact-bar">
    <div class="contact-item">
      <div class="ico"><svg width="26" height="26" viewBox="0 0 24 24"><path d="M5 3l4 1 1 5-2 1.5a12 12 0 006.5 6.5L16 15l5 1 1 4-2 2C10 22 2 14 2 5z" fill="none" stroke="#fff" stroke-width="1.5"/></svg></div>
      <p>CALL US NOW<br>123 456 7890</p>
    </div>
    <div class="contact-item">
      <div class="ico"><svg width="24" height="28" viewBox="0 0 24 28"><path d="M12 27S3 16 3 10a9 9 0 0118 0c0 6-9 17-9 17z" fill="none" stroke="#fff" stroke-width="1.5"/><circle cx="12" cy="10" r="3.5" fill="none" stroke="#fff" stroke-width="1.5"/></svg></div>
      <p>Lorem Ipsum is simply dummy<br>text of the printing.</p>
    </div>
    <div class="contact-item">
      <div class="ico"><svg width="28" height="20" viewBox="0 0 28 20"><rect x="1" y="1" width="26" height="18" fill="none" stroke="#fff" stroke-width="1.5"/><path d="M1 1l13 10L27 1" fill="none" stroke="#fff" stroke-width="1.5"/></svg></div>
      <p>EMAIL US<br>info@qrn-network.com</p>
    </div>
  </div>
  <nav class="abs footer-social" aria-label="Social links">
    <a href="#">Linkora</a><a href="#">Chirpa</a><a href="#">Snapra</a>
  </nav>
  <p class="abs copyright">©QRN_QUILL RIDGE NETWORK LLC. 2018 - All Rights Reserved.</p>
</footer>

</body>
</html>
```